Ledgerwise Forge - WordPress Theme & Logo

Design a logo and Wordpress website design for Ledgerwise Forge. Ledgerwise Forge provides cryptocurrency development services to clients who need a team to create & continue developing a new cryptocurrency or who want to replace their current cryptocurrency development team. more details in the attached document.
Updates

Target Market(s)

Entrepreneurs who are building a business / platform that makes use of an underlying cryptocurrency.

Logo Text

LF or Ledgerwise Forge

Coding

Coded - Design and coding required

Font styles to use
Sans Serif

Requirements
Must have
• Professional logo, complete coded Wordpress theme for all pages, containing all specified links and buttons
Nice to have
• It would be nice if the buttons that are meant to integrate with Dealtrail contain the necessary code for that. I can provide any necessary Dealtrail details from my account.
Should not have
• Slow loading time

```html
<!DOCTYPE html>
<html lang="en">
<head>
<meta charset="utf-8">
<title>Ledgerwise Forge — Cryptocurrency Development</title>
<link href="https://fonts.googleapis.com/css2?family=Montserrat:wght@600;700;800&family=Roboto:wght@400;500;700&display=swap" rel="stylesheet">
<style>
:root{
  --navy:#1d3a63;
  --hero-a:#2f5d99;
  --hero-b:#1f3f6e;
  --band-a:#4f8fd9;
  --band-b:#2c5da4;
  --accent:#3f86d6;
  --ink:#111418;
  --body:#333a44;
  --muted:#f5f5f6;
  --line:#e4e6ea;
  --white:#ffffff;
  --footer-a:#3e67a0;
  --footer-b:#2d4f83;
  --subscribe:#0f54aa;
  --mint:#bfe7ea;
}
*{box-sizing:border-box;margin:0;padding:0}
html,body{width:1200px;height:3280px;overflow:hidden}
body{position:relative;font-family:"Roboto",Arial,sans-serif;color:var(--body);background:var(--white)}
.abs{position:absolute}
a{color:inherit;text-decoration:none}

/* Hero */
.hero{position:absolute;left:0;top:0;width:1200px;height:576px;background:linear-gradient(100deg,var(--hero-a),var(--hero-b));color:var(--white);overflow:hidden}
.brand{font-family:"Montserrat",Arial,sans-serif;font-weight:800;color:var(--white);letter-spacing:-2px}
.hero .brand{left:99px;top:10px;font-size:64px;line-height:72px}
.nav{left:261px;top:36px;font-size:16px;font-weight:500;letter-spacing:.2px}
.nav a{position:absolute;white-space:nowrap}
.flag{left:760px;top:37px;width:36px;height:19px;background:#24418a;border-radius:1px}
.flag::before{content:"";position:absolute;left:15px;top:0;width:6px;height:19px;background:#d6303a}
.flag::after{content:"";position:absolute;left:0;top:7px;width:36px;height:5px;background:#d6303a}
.btn-outline{border:2px solid var(--white);border-radius:30px;color:var(--white);font-family:"Montserrat",Arial,sans-serif;font-weight:700;display:flex;align-items:center;justify-content:center;white-space:nowrap}
.nav-cta{left:824px;top:19px;width:274px;height:54px;font-size:15px}
.hero-title{left:99px;top:174px;width:620px;font-family:"Montserrat",Arial,sans-serif;font-size:31px;line-height:41px;font-weight:700;text-transform:uppercase;letter-spacing:-.2px;white-space:nowrap}
.hero-text{left:99px;top:312px;width:540px;font-size:13.5px;line-height:27px;letter-spacing:-.2px}
.hero-cta{left:102px;top:413px;width:224px;height:53px;font-size:15px}
.hero-art{left:688px;top:96px;width:370px;height:382px;border-radius:50%;background:radial-gradient(circle at 50% 45%,#7fb2ff 0%,#4b7fe0 35%,rgba(47,93,153,0) 70%)}
.scroll-hint{left:590px;top:505px}
.next{left:855px;top:514px;font-size:17px;display:flex;align-items:center;gap:10px}
.slide-num{left:972px;top:488px;font-family:"Montserrat",Arial,sans-serif;font-weight:700;font-size:64px;line-height:72px}
.slide-num small{font-size:30px;font-weight:600;vertical-align:top;position:relative;top:10px}
.slide-next{left:1067px;top:510px}

/* Section headings */
.eyebrow{position:absolute;left:0;width:1200px;text-align:center}
.eyebrow .mark{display:block;font-family:"Montserrat",Arial,sans-serif;font-weight:800;font-size:27px;line-height:28px;color:var(--accent);letter-spacing:-1px}
.eyebrow .label{display:block;font-size:11px;color:var(--accent);text-transform:uppercase;letter-spacing:.4px;margin-top:1px}
.section-title{position:absolute;left:0;width:1200px;text-align:center;font-family:"Montserrat",Arial,sans-serif;font-weight:700;font-size:38px;color:var(--ink)}

/* Why choose */
.why{position:absolute;left:0;top:576px;width:1200px;height:615px;overflow:hidden}
.feature{position:absolute;top:214px;width:322px;height:304px;border:1px solid var(--line);text-align:center;background:var(--white)}
.hex{clip-path:polygon(50% 0,100% 25%,100% 75%,50% 100%,0 75%,0 25%)}
.feature .hex{position:absolute;left:110px;top:39px;width:102px;height:117px;background:var(--navy)}
.feature h3{position:absolute;top:176px;width:100%;font-family:"Montserrat",Arial,sans-serif;font-weight:800;font-size:27px;color:var(--ink)}
.feature p{position:absolute;top:220px;left:30px;right:30px;font-size:15px;line-height:25px;color:var(--body)}

/* About band */
.about{position:absolute;left:0;top:1191px;width:1200px;height:468px;background:linear-gradient(120deg,var(--band-a),var(--band-b));color:var(--white)}
.about-photo{left:102px;top:66px;width:450px;height:343px;background:linear-gradient(135deg,#3a3f4a,#7a5a3a 45%,#c98a3a 55%,#2e3440)}
.about .kicker{left:634px;top:93px;font-size:11px;font-weight:700;letter-spacing:.3px}
.about h2{left:634px;top:113px;font-family:"Montserrat",Arial,sans-serif;font-weight:700;font-size:37px}
.about p{left:634px;top:169px;width:465px;font-size:15px;line-height:27.6px;letter-spacing:-.2px}
.about-cta{left:634px;top:329px;width:155px;height:45px;font-size:15px}

/* Testimonials */
.testimonials{position:absolute;left:0;top:1659px;width:1200px;height:519px;background:var(--muted)}
.review{position:absolute;top:220px;width:323px;height:221px;background:var(--white);border-radius:4px;box-shadow:0 2px 10px rgba(0,0,0,.05);text-align:center}
.avatar{position:absolute;left:113px;top:-42px;width:96px;height:84px;clip-path:polygon(25% 0,75% 0,100% 50%,75% 100%,25% 100%,0 50%);background:linear-gradient(180deg,#b9c6d6,#7e93ad)}
.review h4{position:absolute;top:55px;width:100%;font-family:"Montserrat",Arial,sans-serif;font-weight:700;font-size:13.5px;color:var(--ink);letter-spacing:.3px}
.review .stars{position:absolute;top:73px;width:100%;font-size:9px;color:#f2b21a;letter-spacing:1px}
.review p{position:absolute;top:95px;left:12px;right:12px;font-size:13px;line-height:22.5px;letter-spacing:-.35px;color:var(--body)}
.quote{position:absolute;left:138px;top:195px;width:46px;height:46px;border-radius:50%;background:var(--accent);color:var(--white);font-family:"Montserrat",Arial,sans-serif;font-weight:800;font-size:40px;line-height:60px}

/* Services */
.services{position:absolute;left:0;top:2178px;width:1200px;height:756px;overflow:hidden}
.services .intro{position:absolute;left:180px;top:180px;width:840px;text-align:center;font-size:14.5px;line-height:27.6px;letter-spacing:-.2px;color:var(--body)}
.service{position:absolute;top:306px;width:317px;height:376px;background:var(--white);box-shadow:0 2px 12px rgba(0,0,0,.07)}
.service .thumb{position:absolute;left:6px;top:6px;width:305px;height:208px}
.service h3{position:absolute;top:238px;width:100%;text-align:center;font-family:"Montserrat",Arial,sans-serif;font-weight:700;font-size:19.5px;color:var(--ink)}
.service ul{position:absolute;top:279px;left:72px;list-style:none}
.service li{position:relative;padding-left:22px;font-size:15.5px;line-height:31px;color:var(--body)}
.service li::before{content:"";position:absolute;left:0;top:10px;width:8px;height:8px;border-radius:50%;border:3px solid var(--white);box-shadow:0 0 0 2px var(--accent);background:var(--accent)}

.ring{position:absolute;border-radius:50%;border:1.5px solid var(--mint)}
.glow{position:absolute;width:26px;height:26px;border-radius:50%;background:radial-gradient(circle,#7fd0e0 30%,rgba(127,208,224,0) 75%)}

/* Footer */
.footer{position:absolute;left:0;top:2934px;width:1200px;height:346px;background:linear-gradient(120deg,var(--footer-a),var(--footer-b));color:var(--white)}
.footer .brand{left:99px;top:90px;font-size:64px;line-height:72px}
.social{left:99px;top:192px;display:flex;gap:22px}
.social span{width:18px;height:18px;border:2px solid var(--white);border-radius:4px}
.footer-col{top:68px}
.footer-col h5{font-family:"Montserrat",Arial,sans-serif;font-weight:700;font-size:17.5px;margin-bottom:10px}
.footer-col li{list-style:none;font-size:15px;line-height:33px}
.newsletter{left:808px;top:68px;width:290px}
.newsletter h5{font-family:"Montserrat",Arial,sans-serif;font-weight:700;font-size:17.5px}
.email{position:absolute;top:36px;left:1px;width:287px;height:48px;background:var(--white);border-radius:24px;color:#555;font-size:14.5px;line-height:48px;padding-left:23px}
.subscribe{position:absolute;top:95px;left:1px;width:287px;height:47px;background:var(--subscribe);border-radius:24px;text-align:center;line-height:47px;font-size:16px;font-weight:500;letter-spacing:.3px}
.footer-rule{left:99px;top:289px;width:1002px;height:1px;background:rgba(255,255,255,.35)}
.copyright{left:0;top:312px;width:1200px;text-align:center;font-size:15px}
</style>
</head>
<body>

<header class="hero">
  <div class="abs brand">LF</div>
  <nav class="abs nav">
    <a style="left:0">ABOUT US</a>
    <a style="left:121px">OUR SERVICES</a>
    <a style="left:273px">TESTIMONIALS</a>
    <a style="left:429px">BLOG</a>
  </nav>
  <div class="abs flag" aria-label="Language: English"></div>
  <a class="abs btn-outline nav-cta">Schedule a Free Consultation</a>

  <h1 class="abs hero-title">Your own cryptocurrency.<br>Secure, easy to use, and built<br>by an expert team.</h1>
  <p class="abs hero-text">Ledgerwise Forge adds professionalism to cryptocurrency development. Our done-for-you service covers everything from development and IT operations to ongoing support. You haveaccess to a full team, for less than the typical cost of a single developer</p>
  <a class="abs btn-outline hero-cta">Free Consultation</a>

  <div class="abs hero-art" role="img" aria-label="Illustration of glowing blue crystal blocks surrounded by floating coin tokens"></div>

  <svg class="abs scroll-hint" width="20" height="42" viewBox="0 0 20 42" fill="none" stroke="#fff" stroke-width="1.6">
    <rect x="2" y="1" width="16" height="26" rx="8"/><line x1="10" y1="7" x2="10" y2="13"/><polyline points="6,34 10,38 14,34"/>
  </svg>
  <div class="abs next">Next
    <svg width="28" height="14" viewBox="0 0 28 14" fill="none" stroke="#fff" stroke-width="1.6"><line x1="1" y1="7" x2="26" y2="7"/><polyline points="20,1 26,7 20,13"/></svg>
  </div>
  <div class="abs slide-num">01<small>/</small></div>
  <svg class="abs slide-next" width="30" height="30" viewBox="0 0 30 30" fill="none" stroke="#fff" stroke-width="1.6"><circle cx="15" cy="15" r="13.5"/><polyline points="12,9 18,15 12,21"/></svg>
</header>

<section class="why">
  <div class="ring" style="left:1113px;top:300px;width:260px;height:320px"></div>
  <div class="glow" style="left:1114px;top:542px"></div>
  <div class="eyebrow" style="top:92px"><span class="mark">LF</span><span class="label">Why choose us</span></div>
  <h2 class="section-title" style="top:138px">Why choose Ledgerwise Forge</h2>

  <article class="feature" style="left:100px">
    <div class="hex"><svg width="102" height="117" viewBox="0 0 102 117" fill="none" stroke="#fff" stroke-width="2"><circle cx="56" cy="48" r="13"/><path d="M28 66h14l10 6h18v6H50M28 78h10l18 6 18-10"/></svg></div>
    <h3>Value</h3>
    <p>A team of experts, regular updates, and fixed costs</p>
  </article>
  <article class="feature" style="left:439px">
    <div class="hex"><svg width="102" height="117" viewBox="0 0 102 117" fill="none" stroke="#fff" stroke-width="2"><circle cx="50" cy="56" r="12"/><path d="M32 58a18 18 0 0 1 36 0M30 56v8h5v-8zM66 56v8h5v-8z"/><rect x="60" y="34" width="16" height="10" rx="2"/></svg></div>
    <h3>Support</h3>
    <p>Receive advice and other services, beyond development.</p>
  </article>
  <article class="feature" style="left:778px">
    <div class="hex"><svg width="102" height="117" viewBox="0 0 102 117" fill="none" stroke="#fff" stroke-width="2"><circle cx="51" cy="44" r="8"/><circle cx="36" cy="62" r="5"/><circle cx="66" cy="62" r="5"/><path d="M28 80v-6a8 8 0 0 1 16 0v6M58 80v-6a8 8 0 0 1 16 0v6M42 80h18"/></svg></div>
    <h3>Commitment</h3>
    <p>Enjoy regular updates and<br>new features</p>
  </article>
</section>

<section class="about">
  <div class="abs about-photo" role="img" aria-label="Photo of business people using a phone and tablet with glowing finance icons overlaid"></div>
  <div class="abs kicker">ABOUT US</div>
  <h2 class="abs">Who We Are</h2>
  <p class="abs">in addition to creating and enhancing cryptocurrencies for clients, the Ledgerwise Forge team has been running the Corvane cryptocurrency since 2017. We prefer long-term relationships, enabling us to deliver the very highest quality and giving you peace of mind that you’ve got a professional and trustworthy team at your side.</p>
  <a class="abs btn-outline about-cta">Learn More</a>
</section>

<section class="testimonials">
  <div class="eyebrow" style="top:78px"><span class="mark">LF</span><span class="label">Client review</span></div>
  <h2 class="section-title" style="top:117px">Testimonials</h2>

  <article class="review" style="left:99px">
    <div class="avatar" role="img" aria-label="Client portrait"></div>
    <h4>JOHN SMITH</h4><div class="stars">★★★★★</div>
    <p>At vero eos et accusamus etto odio dignissimos ducimus qui blanditiis praesentium voluptatum deleniti atque corrupti qures et quas molestias excepturi sint occaecati</p>
    <div class="quote">“</div>
  </article>
  <article class="review" style="left:438px">
    <div class="avatar" role="img" aria-label="Client portrait"></div>
    <h4>JOHN SMITH</h4><div class="stars">★★★★★</div>
    <p>At vero eos et accusamus etto odio dignissimos ducimus qui blanditiis praesentium voluptatum deleniti atque corrupti qures et quas molestias excepturi sint occaecati</p>
    <div class="quote">“</div>
  </article>
  <article class="review" style="left:777px">
    <div class="avatar" role="img" aria-label="Client portrait"></div>
    <h4>JOHN SMITH</h4><div class="stars">★★★★★</div>
    <p>At vero eos et accusamus etto odio dignissimos ducimus qui blanditiis praesentium voluptatum deleniti atque corrupti qures et quas molestias excepturi sint occaecati</p>
    <div class="quote">“</div>
  </article>
</section>

<section class="services">
  <div class="ring" style="left:-200px;top:-20px;width:325px;height:330px"></div>
  <div class="ring" style="left:-240px;top:90px;width:320px;height:320px"></div>
  <div class="glow" style="left:-3px;top:97px"></div>
  <div class="glow" style="left:100px;top:206px"></div>
  <div class="eyebrow" style="top:68px"><span class="mark">LF</span><span class="label">Our service</span></div>
  <h2 class="section-title" style="top:108px">What We Do</h2>
  <p class="intro">Ledgerwise Forge offers more than just development. We provide a complete solution and our clients receive access to expert advice, ongoing support, I.T. operations, mobile wallets, and even the creation of white papers, Our packages can be tailored to suit you to match your requirements or budget, you can simply pick and choose the features you would like. Alternatively, We can create a custom package just for you.</p>

  <article class="service" style="left:101px">
    <div class="thumb" role="img" aria-label="Photo of a tablet showing a rocket launch chart on a wooden desk" style="background:linear-gradient(135deg,#6b5a4a,#1e1e22 45%,#3a3a3e)"></div>
    <h3>Blockchain creation &amp; Launch</h3>
    <ul><li>This is a list item</li><li>Another list item</li><li>Yup, another list item</li></ul>
  </article>
  <article class="service" style="left:442px">
    <div class="thumb" role="img" aria-label="Photo of a hand touching a glowing crypto interface" style="background:linear-gradient(135deg,#4a3a30,#a0805e 50%,#2b2420)"></div>
    <h3>Basic</h3>
    <ul><li>This is a list item</li><li>Another list item</li><li>Yup, another list item</li></ul>
  </article>
  <article class="service" style="left:783px">
    <div class="thumb" role="img" aria-label="Photo of a trader using a laptop and phone with market charts" style="background:linear-gradient(135deg,#5a4a3e,#2a2d35 50%,#a08a72)"></div>
    <h3>Mid-range</h3>
    <ul><li>This is a list item</li><li>Another list item</li><li>Yup, another list item</li></ul>
  </article>
</section>

<footer class="footer">
  <div class="abs brand">LF</div>
  <div class="abs social" aria-label="Social links"><span></span><span></span><span></span><span></span></div>
  <div class="abs footer-col" style="left:357px">
    <h5>Site Content</h5>
    <ul><li>Home</li><li>About</li><li>Feature</li><li>Pricing</li><li>Contact</li></ul>
  </div>
  <div class="abs footer-col" style="left:581px">
    <h5>Major Topics</h5>
    <ul><li>Search</li><li>T&amp;Cs</li><li>Privacy</li><li>Commu</li></ul>
  </div>
  <div class="abs newsletter">
    <h5>Get our Newsletter</h5>
    <div class="email">Enter your email</div>
    <div class="subscribe">SUBSCRIBE</div>
  </div>
  <div class="abs footer-rule"></div>
  <div class="abs copyright">Copyright © 2021 Ledgerwise Forge. All rights reserved.</div>
</footer>

</body>
</html>
```